VKT Consulting

Government/Entitlement Consulting Services- I assist developers obtain entitlements from local, state and federal government agencies so that they can build their projects. Often these projects are very complicated and political and may face community opposition.

Target Market(s)

Real Estate Developers

Industry/Entity Type

Business Consultant

Contact Information for Business Card

Dana Melbrook
Principal

Font styles to use
Serif
Sans Serif

Requirements
Must have
• Classy and professional appeal.
Nice to have
• I like a combination of a mat and glossy finish. I've seen that done with black and then a bold color for a pop, but am not 100% committed to that.

```html
<!DOCTYPE html>
<html lang="en">
<head>
<meta charset="utf-8">
<title>VKT Consulting – Business Card</title>
<link href="https://fonts.googleapis.com/css2?family=Arimo:wght@400;700&display=swap" rel="stylesheet">
<style>
  :root{
    --page:#d9d9d7;
    --ink-black:#050505;
    --paper-light:#e7e7e3;
    --band-grey:#9ea2a0;
    --wedge-grey:#3b3c3f;
    --text-dark:#1c1c1c;
    --text-light:#f2f2f2;
  }
  *{margin:0;padding:0;box-sizing:border-box}
  html,body{width:1200px;height:864px;overflow:hidden;background:var(--page)}
  body{font-family:"Arimo",Arial,sans-serif;position:relative}
  .card{position:absolute;left:300px;width:600px;height:343px;overflow:hidden;
        box-shadow:0 4px 14px rgba(0,0,0,.18)}
  .card--front{top:52px;background:var(--paper-light)}
  .card--back{top:469px;background:var(--ink-black);display:flex;align-items:center;justify-content:center}
  .card__shapes{position:absolute;inset:0;width:100%;height:100%}
  .holder{position:absolute;left:42px;top:52px;color:var(--text-dark)}
  .holder__name{font-size:20px;font-weight:400;line-height:1.1}
  .holder__title{font-size:14px;margin-top:2px}
  .company{color:var(--text-light);font-weight:700}
  .card--front .company{position:absolute;left:300px;top:96px;font-size:29px}
  .card--back .company{font-size:46px;letter-spacing:.2px}
  .contacts{position:absolute;left:250px;top:176px;list-style:none;color:var(--text-light);font-size:15px;line-height:23px}
  .contacts li{display:flex;align-items:center;gap:10px}
  .contacts svg{width:12px;height:12px;flex:none;fill:var(--text-light)}
</style>
</head>
<body>
  <section class="card card--front">
    <svg class="card__shapes" viewBox="0 0 600 343" preserveAspectRatio="none" aria-hidden="true">
      <defs>
        <linearGradient id="wedgeShade" x1="0" y1="0" x2="1" y2="1">
          <stop offset="0" stop-color="#2a2b2e"/>
          <stop offset="1" stop-color="#55575b"/>
        </linearGradient>
      </defs>
      <polygon points="205,0 262,0 60,343 12,343" fill="var(--band-grey)"/>
      <polygon points="0,322 30,343 0,343" fill="var(--wedge-grey)"/>
      <polygon points="262,0 600,0 600,343 60,343" fill="var(--ink-black)"/>
      <polygon points="548,0 600,0 600,343 582,343" fill="url(#wedgeShade)"/>
    </svg>
    <div class="holder">
      <p class="holder__name">Dana Melbrook</p>
      <p class="holder__title">Principal</p>
    </div>
    <p class="company">VKT Consulting</p>
    <ul class="contacts">
      <li><svg viewBox="0 0 12 12"><path d="M2.5 0.5l2 2.6-1.1 1.3c.7 1.6 1.9 2.8 3.5 3.5l1.3-1.1 2.6 2-1.2 2.2C4.8 10.8 1 7 .3 1.7z"/></svg>512-555-0147</li>
      <li><svg viewBox="0 0 12 12"><path d="M0 2h12v1L6 7 0 3z M0 4.3l6 4 6-4V10H0z"/></svg>www.vktconsulting.com</li>
      <li><svg viewBox="0 0 12 12"><path d="M6 0a6 6 0 1 0 0 12A6 6 0 0 0 6 0zm0 1.2c.6.7 1.1 2 1.2 4.2H4.8C4.9 3.2 5.4 1.9 6 1.2zM1.3 5.4a4.8 4.8 0 0 1 2.4-3.6c-.5.9-.8 2.200-.9 3.6zm0 1.2h1.5c.1 1.4.4 2.7.9 3.6a4.8 4.8 0 0 1-2.4-3.6zM6 10.8c-.6-.7-1.1-2-1.2-4.2h2.4c-.1 2.2-.6 3.5-1.2 4.2zm2.3-.6c.5-.9.8-2.2.9-3.6h1.5a4.8 4.8 0 0 1-2.4 3.6zm.9-4.8c-.1-1.4-.4-2.7-.9-3.6a4.8 4.8 0 0 1 2.4 3.6z"/></svg>info@vktconsulting.com</li>
      <li><svg viewBox="0 0 12 12"><path d="M6 0a4 4 0 0 1 4 4c0 3-4 8-4 8S2 7 2 4a4 4 0 0 1 4-4zm0 2.3a1.7 1.7 0 1 0 0 3.4 1.7 1.7 0 0 0 0-3.4z"/></svg>14 Harlow Lane Penrith NSW 2750</li>
    </ul>
  </section>

  <section class="card card--back">
    <p class="company">VKT Consulting</p>
  </section>
</body>
</html>
```